Event Website Design

We need a new website design for an events driven website. The domain for this site is http://brackmoorhalls.co.uk. The site is up and running but needs a new fresh, modern look.
I've attached a Balamiq Mockup for the layout of the home page. Also attached is a png of the logo.
Key colours for the site are 0f7e6a, 35bde, d57835 & 373737.
Font to use is Proxima Nova
Width of the site should be 1200px
The design should be contemporary with minimal clutter.
Websites to references are…
http://vorpin.london/
http://www.darvushall.co.uk/
These are just guidelines, please feel free to use you own creative judgment.
The selected design file needs to be supplied as an editable PSD.
Reason: I've submitted 5 designs to the client, who will select the one they want. I will then choose that design. So please be patient as I'm waiting for a decision from my client.
Industry/Entity Type
Events
Number of Pages Required
1 page
Look and feel
Each slider illustrates characteristics of the customer's brand and the style your logo design should communicate.

```html
<!DOCTYPE html>
<html lang="en">
<head>
<meta charset="utf-8">
<title>Brackmoor Halls – Entertainment &amp; Sports Centre</title>
<link href="https://fonts.googleapis.com/css2?family=Montserrat:wght@400;500;600;700&display=swap" rel="stylesheet">
<style>
:root{
  --orange:#d57835;
  --teal:#0f7e6a;
  --blue:#1a5fd6;
  --sky:#35a8de;
  --dark:#373737;
  --darker:#2b2b2b;
  --light:#f4f4f4;
  --card:#ececec;
  --text:#333;
  --white:#fff;
}
*{box-sizing:border-box;margin:0;padding:0}
html,body{width:1200px;height:2267px;overflow:hidden}
body{position:relative;font-family:"Montserrat",Arial,sans-serif;color:var(--text);background:var(--white)}
a{color:inherit;text-decoration:none}

/* header */
.site-header{position:absolute;left:0;top:0;width:1200px;height:112px;background:linear-gradient(#3d3d3d,#303030)}
.brand{position:absolute;left:162px;top:30px;color:var(--white);font-weight:700;font-size:18px;line-height:21px;letter-spacing:.5px;display:flex;align-items:center;gap:9px}
.brand-mark{flex:none;width:14px;height:14px;background:var(--sky);border-radius:50%}
.tagline{position:absolute;left:335px;top:40px;color:var(--sky);font-size:15px;line-height:17px}
.tagline small{display:block;font-size:11px}
.util-links{position:absolute;right:162px;top:12px;display:flex;font-size:10px;color:#ddd}
.util-links span{padding:0 12px;border-left:1px solid #777}
.util-links span:first-child{border:none}
.util-links span:last-child{padding-right:0}
.box-office{position:absolute;right:162px;top:36px;display:flex;align-items:center;gap:14px;color:var(--orange);font-size:18px;font-weight:500}
.box-office .icon{width:26px;height:26px;border-radius:50%;background:var(--orange);display:flex;align-items:center;justify-content:center}
.search{position:absolute;left:843px;top:70px;width:92px;height:24px;border-bottom:1px solid #555;color:#ddd;font-size:11px;display:flex;justify-content:space-between;align-items:center}
.socials{position:absolute;left:952px;top:76px;display:flex;gap:12px}

/* nav */
.main-nav{position:absolute;left:0;top:112px;width:1200px;height:45px;background:var(--orange);display:flex;padding-left:172px}
.main-nav a{color:var(--white);font-size:11px;font-weight:600;line-height:45px;padding:0 9px}
.main-nav a.active{background:var(--dark);padding:0 16px}

/* hero */
.hero{position:absolute;left:0;top:157px;width:1200px;height:473px;background:linear-gradient(90deg,#3a3230 0%,#4a3a36 35%,#8a7468 55%,#c7b9b6 70%,#7b5a52 90%,#4c3630 100%)}
.hero-copy{position:absolute;left:162px;top:180px;color:var(--white);width:380px}
.hero-kicker{font-size:18px;font-weight:500}
.hero-title{font-size:31px;font-weight:600;margin-top:6px}
.hero-date{font-size:14px;font-weight:600;margin-top:6px}
.hero-text{font-size:10px;line-height:17px;margin-top:6px}
.btn-outline{position:absolute;top:321px;height:30px;border:2px solid var(--white);border-radius:3px;color:var(--white);font-size:14px;display:flex;align-items:center;justify-content:center}
.btn-outline.more{left:160px;width:85px;border-color:var(--orange);color:var(--orange)}
.btn-outline.book{left:252px;width:85px}
.scroll-down{position:absolute;left:175px;top:387px}

/* shows */
.shows{position:absolute;left:0;top:630px;width:1200px;height:292px;background:var(--white)}
.slider-arrow{position:absolute;top:84px;width:24px;height:26px;background:#ddd;display:flex;align-items:center;justify-content:center}
.show-card{position:absolute;top:30px;width:209px;height:230px;background:var(--card);box-shadow:0 2px 2px rgba(0,0,0,.15)}
.show-img{height:139px}
.show-title{font-size:15px;font-weight:500;margin:12px 0 0 15px;color:#222}
.show-date{font-size:9px;margin:3px 0 0 18px}
.show-actions{display:flex;gap:6px;margin:10px 0 0 18px}
.btn-sm{display:inline-block;font-size:9px;color:var(--white);height:19px;line-height:19px;width:60px;text-align:center}
.btn-sm.orange{background:var(--orange)}
.btn-sm.teal{background:var(--teal)}
.btn-sm.blue{background:var(--blue)}
.btn-sm.dark{background:#444}

/* news */
.news{position:absolute;left:0;top:922px;width:1200px;height:300px;background:var(--light)}
.news-heading{position:absolute;left:167px;top:26px;font-size:14px;font-weight:500;color:#222}
.see-all{position:absolute;left:167px;top:47px;width:188px;font-size:9px;color:var(--blue);font-weight:600;border-bottom:1px solid var(--blue);padding-bottom:2px}
.news-item{position:absolute;top:86px;width:255px}
.news-item h3{font-size:15px;font-weight:600;color:#111}
.news-item p{font-size:9px;line-height:18px;margin-top:10px}
.news-meta{font-size:10px;margin-top:10px;color:#444;display:flex;gap:8px;align-items:center}
.news-item .btn-sm{width:82px;margin-top:14px}

/* features */
.features{position:absolute;left:0;top:1222px;width:1200px;height:384px;background:var(--orange)}
.feature-icon{position:absolute;top:34px;width:66px;height:66px;border:2px solid var(--white);border-radius:50%;display:flex;align-items:center;justify-content:center}
.feature-label{position:absolute;top:115px;width:290px;text-align:center;color:var(--white);font-size:14px;font-weight:500}
.feature-img{position:absolute;top:155px;height:185px}
.feature-img .btn-sm{position:absolute;left:12px;bottom:13px}

/* sports */
.sports{position:absolute;left:0;top:1606px;width:1200px;height:452px;background:radial-gradient(ellipse at 60% 55%,#8a7a4e 0%,#5f5a4e 45%,#4a4a48 100%)}
.sports h2{position:absolute;left:0;width:1200px;top:166px;text-align:center;color:var(--white);font-size:30px;font-weight:500}
.sports .cta{position:absolute;left:434px;top:210px;width:332px;height:41px;border:2px solid var(--white);border-radius:3px;color:var(--white);font-size:15px;font-weight:500;display:flex;align-items:center;justify-content:center}

/* footer */
.site-footer{position:absolute;left:0;top:2058px;width:1200px;height:180px;background:var(--light)}
.footer-heading{position:absolute;top:38px;font-size:11px;font-weight:600;color:#111;letter-spacing:.5px}
.footer-list{position:absolute;top:62px;list-style:none;font-size:9.5px;font-weight:500;line-height:18px;color:#222}
.footer-list.arrows li::before{content:"›";margin-right:14px;font-weight:700}
.footer-brand{position:absolute;left:836px;top:62px;font-size:18px;line-height:21px;font-weight:700;color:var(--dark);letter-spacing:.5px;display:flex;align-items:center;gap:9px}
.footer-brand .brand-mark{background:var(--teal)}
.bottom-bar{position:absolute;left:0;top:2238px;width:1200px;height:29px;background:#e6e6e6}
.bottom-socials{position:absolute;left:204px;top:8px;display:flex;gap:3px}
.bottom-socials span{width:14px;height:14px;border-radius:50%}
.copyright{position:absolute;left:768px;top:9px;font-size:9px;color:#333}
</style>
</head>
<body>

<header class="site-header">
  <div class="brand"><span class="brand-mark"></span><span>BRACKMOOR<br>HALLS</span></div>
  <div class="tagline">WESSMERE'S PREMIER<small>Entertainment &amp; Sports Center</small></div>
  <nav class="util-links"><span>Gift Voucher</span><span>Join Our Mailing List</span><span>My Account</span><span>Basket</span><span>Register</span></nav>
  <div class="box-office">
    <span class="icon"><svg width="12" height="12" viewBox="0 0 24 24"><path fill="#fff" d="M6.6 10.8a15 15 0 006.6 6.6l2.2-2.2c.3-.3.7-.4 1-.2 1.1.4 2.3.6 3.6.6.6 0 1 .4 1 1V20c0 .6-.4 1-1 1A17 17 0 013 4c0-.6.4-1 1-1h3.5c.6 0 1 .4 1 1 0 1.3.2 2.5.6 3.6.1.3 0 .7-.2 1z"/></svg></span>
    <span>Box Office&nbsp; :&nbsp; 01632 960 410</span>
  </div>
  <div class="search">Search
    <svg width="11" height="11" viewBox="0 0 24 24"><circle cx="10" cy="10" r="7" fill="none" stroke="#ddd" stroke-width="3"/><path d="M15 15l6 6" stroke="#ddd" stroke-width="3"/></svg>
  </div>
  <div class="socials">
    <svg width="10" height="10"><path d="M3 10V5H1V3h2V2c0-1 1-2 2-2h2v2H5v1h2l-.3 2H5v5z" fill="#ddd"/></svg>
    <svg width="10" height="10"><path d="M0 8l10-7-3 9z" fill="#ddd"/></svg>
    <svg width="10" height="10"><rect x="0.5" y="1.5" width="9" height="8" fill="none" stroke="#ddd"/><path d="M0 4h10" stroke="#ddd"/></svg>
  </div>
</header>

<nav class="main-nav">
  <a class="active">WHAT'S ON</a><a>CONFERENCING AND EVENTS</a><a>SPORTS &amp; LEISURE</a><a>LANTERN THEATRE</a><a>PLAN YOUR VISIT</a><a>NEWS</a><a>DISCOVER MORE</a><a>CONTACT US</a>
</nav>

<section class="hero" role="img" aria-label="Ballet dancers in ornate costumes performing on stage">
  <div class="hero-copy">
    <div class="hero-kicker">STAGE LIVE SCREENING:</div>
    <div class="hero-title">THE SLEEPING BEAUTY</div>
    <div class="hero-date">Wed 29 Mar 2017</div>
    <p class="hero-text">A perennial delight and a much-loved classic, the Company's The Sleeping Beauty combines the best of classical ballet, with all its charms...</p>
  </div>
  <a class="btn-outline more">MORE</a>
  <a class="btn-outline book">BOOK</a>
  <svg class="scroll-down" width="54" height="54"><circle cx="27" cy="27" r="25" fill="none" stroke="#222" stroke-width="2"/><path d="M17 23l10 10 10-10" fill="none" stroke="#222" stroke-width="2"/></svg>
</section>

<section class="shows">
  <div class="slider-arrow" style="left:133px"><svg width="8" height="12"><path d="M7 1L2 6l5 5" fill="none" stroke="#777" stroke-width="1.5"/></svg></div>
  <div class="slider-arrow" style="left:1040px"><svg width="8" height="12"><path d="M1 1l5 5-5 5" fill="none" stroke="#777" stroke-width="1.5"/></svg></div>

  <article class="show-card" style="left:162px">
    <div class="show-img" role="img" aria-label="Ballet performance scene" style="background:linear-gradient(135deg,#6a4a3e,#c9b2a8 60%,#8a6a5a)"></div>
    <h3 class="show-title">SHOW TITILE</h3><div class="show-date">Wed 29 Mar 2017</div>
    <div class="show-actions"><a class="btn-sm orange">MORE</a><a class="btn-sm teal">BOOK</a></div>
  </article>
  <article class="show-card" style="left:384px">
    <div class="show-img" role="img" aria-label="Period drama stage production" style="background:linear-gradient(135deg,#3f8a88,#c8b79a 55%,#5c8c7a)"></div>
    <h3 class="show-title">SHOW TITILE</h3><div class="show-date">Wed 29 Mar 2017</div>
    <div class="show-actions"><a class="btn-sm orange">MORE</a><a class="btn-sm teal">BOOK</a></div>
  </article>
  <article class="show-card" style="left:606px">
    <div class="show-img" role="img" aria-label="Musical dance troupe under stage lights" style="background:linear-gradient(135deg,#d0702a,#3a1a1e 50%,#b03040)"></div>
    <h3 class="show-title">SHOW TITILE</h3><div class="show-date">Wed 29 Mar 2017</div>
    <div class="show-actions"><a class="btn-sm orange">MORE</a><a class="btn-sm teal">BOOK</a></div>
  </article>
  <article class="show-card" style="left:828px">
    <div class="show-img" role="img" aria-label="Performer holding a fan against a purple backdrop" style="background:linear-gradient(135deg,#a65ad0,#e8c8e0 55%,#9a4ac8)"></div>
    <h3 class="show-title">SHOW TITILE</h3><div class="show-date">Wed 29 Mar 2017</div>
    <div class="show-actions"><a class="btn-sm orange">MORE</a><a class="btn-sm teal">BOOK</a></div>
  </article>
</section>

<section class="news">
  <h2 class="news-heading">LATEST FROM BRACKMOOR</h2>
  <a class="see-all">See All News</a>

  <article class="news-item" style="left:177px">
    <h3>Hampden-Sydney</h3>
    <p>Lorem Ipsum generators on the Internet tend to repeat pre-defined chunks as necessary, making this the first true generator on the Internet. It uses a dictionary of over 200 Latin words,</p>
    <div class="news-meta">💬 Comments : 23 &nbsp;▦ Date : 23/Nov/2016</div>
    <a class="btn-sm teal">READ MORE</a>
  </article>
  <article class="news-item" style="left:474px">
    <h3>Finibus Bonorum</h3>
    <p>Lorem Ipsum generators on the Internet tend to repeat pre-defined chunks as necessary, making this the first true generator on the Internet. It uses a dictionary of over 200 Latin words,</p>
    <div class="news-meta">💬 Comments : 23 &nbsp;▦ Date : 23/Nov/2016</div>
    <a class="btn-sm blue">READ MORE</a>
  </article>
  <article class="news-item" style="left:772px">
    <h3>Nam libero tempore</h3>
    <p>Lorem Ipsum generators on the Internet tend to repeat pre-defined chunks as necessary, making this the first true generator on the Internet. It uses a dictionary of over 200 Latin words,</p>
    <div class="news-meta">💬 Comments : 23 &nbsp;▦ Date : 23/Nov/2016</div>
    <a class="btn-sm blue">READ MORE</a>
  </article>
</section>

<section class="features">
  <div class="feature-icon" style="left:271px"><svg width="28" height="34" viewBox="0 0 28 34"><rect x="9" y="2" width="10" height="18" rx="5" fill="none" stroke="#fff" stroke-width="2"/><path d="M4 15a10 10 0 0020 0M14 25v6M9 32h10" fill="none" stroke="#fff" stroke-width="2"/></svg></div>
  <div class="feature-label" style="left:159px">CONFERENCES &amp; EVENTS</div>
  <div class="feature-icon" style="left:566px"><svg width="34" height="34" viewBox="0 0 34 34"><path d="M6 8l8 3-2 9-7-3zM28 8l-8 3 2 9 7-3zM9 20l-2 10M25 20l2 10M4 31h6M24 31h6" fill="none" stroke="#fff" stroke-width="2"/></svg></div>
  <div class="feature-label" style="left:455px">PARTIES AT BRACKMOOR</div>
  <div class="feature-icon" style="left:862px"><svg width="34" height="30" viewBox="0 0 34 30"><rect x="2" y="2" width="22" height="15" rx="2" fill="none" stroke="#fff" stroke-width="2"/><path d="M10 20v3h16l5 4v-4h1V9h-5M7 7h12M7 11h9" fill="none" stroke="#fff" stroke-width="2"/></svg></div>
  <div class="feature-label" style="left:750px">CO-WORKING HUB</div>

  <div class="feature-img" role="img" aria-label="Speaker presenting to a conference audience" style="left:162px;width:285px;background:linear-gradient(135deg,#1a2a4a,#c0502a 60%,#6a2a1a)"><a class="btn-sm orange">MORE</a></div>
  <div class="feature-img" role="img" aria-label="Friends celebrating at a party with drinks" style="left:458px;width:284px;background:linear-gradient(135deg,#7a3ab0,#e0a070 50%,#3a8ad0)"><a class="btn-sm dark">MORE</a></div>
  <div class="feature-img" role="img" aria-label="Colleagues toasting with coffee cups in a shared workspace" style="left:752px;width:286px;background:linear-gradient(135deg,#506a80,#c8b8a8 50%,#d8c040)"><a class="btn-sm dark">MORE</a></div>
</section>

<section class="sports" role="img" aria-label="Group white-water rafting with paddles">
  <h2>SPORTS &amp; LEISURE</h2>
  <a class="cta">CLICK HERE FOR MORE INFORMATION</a>
</section>

<footer class="site-footer">
  <h4 class="footer-heading" style="left:202px">CONTACT ADDRESS</h4>
  <ul class="footer-list" style="left:202px">
    <li><svg width="9" height="10" viewBox="0 0 10 12" style="margin-right:8px"><path d="M5 0a4 4 0 014 4c0 3-4 8-4 8S1 7 1 4a4 4 0 014-4z" fill="#222"/></svg>Brackmoor Entertainments Venue</li>
    <li style="padding-left:17px">Fernbrook Close</li>
    <li style="padding-left:17px">Brackmoor</li>
    <li style="padding-left:17px">Wessmere</li>
    <li style="padding-left:17px">BX10 4QT</li>
  </ul>
  <h4 class="footer-heading" style="left:491px">QUICK LINKS</h4>
  <ul class="footer-list arrows" style="left:494px">
    <li>What's on</li><li>Conferencing &amp; Events</li><li>Sports &amp; Leisure</li><li>Lantern Theatre</li>
  </ul>
  <ul class="footer-list arrows" style="left:639px">
    <li>Plan Your Visit</li><li>News</li><li>Discover More</li><li>Contact Us</li>
  </ul>
  <div class="footer-brand"><span class="brand-mark"></span><span>BRACKMOOR<br>HALLS</span></div>
</footer>

<div class="bottom-bar">
  <div class="bottom-socials"><span style="background:#2a4a9a"></span><span style="background:#2aa0e0"></span><span style="background:#d03030"></span><span style="background:#b08a50"></span></div>
  <div class="copyright">© 2016 .www.companyname.com&nbsp; |&nbsp; All Rights Reserved.</div>
</div>

</body>
</html>
```